The design should look similar to the uploaded example to accommodate the information needed for a business card template. I would like to see the colors orange and charcoal grey incorporated along with the logo.The following should be on the back of the card SPECIALIZING IN NEW AND USED TIRES & WHEELS FOR:- Loaders- Skid Steers- Telehandlers- Boom Lifts- Forklifs and moreELIMINATING DOWNTIMEWheel Exchange Program for New & Used Foam Filled and Solid Rubber TiresSPECIALTY SERVICES- Foam Filling Tires- Largest Tire Press in SE- ONSITE Forklift Tire Press- Boom Truck Services - Rubber Tracks

Target Market(s)

New and Existing Customers

Industry/Entity Type

Business

Contact Information for Business Card

NAMEHEAVY DUTY TIRE, LLC8470 Belvedere RoadWest Palm Beach, FL 33411P: 844-HD-TIRESF: 561-431-6469C:E: W: WWW.GRANITERIMSUPPLY-EXAMPLE.COM

Font styles to use
Sans Serif

Colors
f37122
333333

Requirements
Must have
• The logo and the information indicated for the backside of the card
Nice to have
• Keep the orange and charcoal grey colors

```html
<!DOCTYPE html>
<html lang="en">
<head>
<meta charset="utf-8">
<title>Granite Rim Supply – Business Card</title>
<link href="https://fonts.googleapis.com/css2?family=Source+Sans+3:wght@400;600;700;900&display=swap" rel="stylesheet">
<style>
  :root {
    --orange: #f37122;
    --orange-card: #fb8a3e;
    --orange-watermark: #f48231;
    --charcoal: #333333;
    --card-white: #f3f3f3;
    --ink: #1d1d1d;
    --white: #ffffff;
    --backdrop-top: #2a2a2a;
    --backdrop-bottom: #050505;
  }
  * { margin: 0; padding: 0; box-sizing: border-box; }
  html, body { width: 1200px; height: 900px; overflow: hidden; }
  body {
    position: relative;
    background: linear-gradient(180deg, var(--backdrop-top) 0%, #1c1c1c 55%, var(--backdrop-bottom) 100%);
    font-family: "Source Sans 3", "Myriad Pro", sans-serif;
  }
  .card {
    position: absolute;
    top: 184px;
    height: 490px;
    border-radius: 12px;
    overflow: hidden;
    text-align: center;
  }
  .card-front { left: 299px; width: 301px; background: var(--card-white); }
  .card-back { left: 645px; width: 305px; background: var(--orange-card); color: var(--white); }

  .brand { position: absolute; top: 222px; left: 0; right: 0; top: 38px; }
  .brand-dot {
    width: 92px; height: 92px; border-radius: 50%;
    background: var(--charcoal); margin: 0 auto;
  }
  .brand-name {
    margin-top: 12px; font-size: 21px; font-weight: 700;
    color: var(--charcoal); letter-spacing: 0.5px;
  }

  .person-name {
    position: absolute; left: 0; right: 0; top: 212px;
    font-size: 19px; font-weight: 600; color: var(--orange); letter-spacing: 0.3px;
  }
  .company {
    position: absolute; left: 0; right: 0; top: 264px;
    font-size: 15.5px; font-weight: 600; color: var(--orange);
  }
  .address {
    position: absolute; left: 0; right: 0; top: 287px;
    font-size: 14px; line-height: 20px; color: var(--ink);
  }
  .contact-list {
    position: absolute; left: 0; right: 0; top: 351px;
    list-style: none; font-size: 14px; line-height: 20.5px; color: var(--ink);
  }
  .contact-list li { display: flex; justify-content: center; align-items: center; gap: 4px; }
  .contact-list svg { width: 10px; height: 10px; fill: var(--orange); flex: none; }

  .watermark {
    position: absolute; left: 0; right: 0; top: 142px;
    font-size: 78px; font-weight: 900; line-height: 92px;
    color: var(--orange-watermark); letter-spacing: 2px;
  }
  .back-block { position: absolute; left: 0; right: 0; }
  .back-heading { font-size: 15.5px; font-weight: 600; line-height: 20px; }
  .back-heading.lg { font-size: 17.5px; }
  .back-list { list-style: none; font-size: 15.5px; font-weight: 600; }
  .specializing { top: 38px; }
  .specializing .back-list { margin-top: 10px; line-height: 20px; }
  .specialty { top: 207px; }
  .specialty .back-list { margin-top: 6px; line-height: 22px; }
  .downtime { top: 382px; }
  .downtime p { font-size: 15.5px; font-weight: 600; line-height: 20px; }
</style>
</head>
<body>
  <section class="card card-front" aria-label="Card front">
    <div class="brand">
      <div class="brand-dot"></div>
      <div class="brand-name">GRANITE RIM</div>
    </div>
    <h1 class="person-name">MARCUS DELANEY</h1>
    <h2 class="company">GRANITE RIM SUPPLY, LLC</h2>
    <p class="address">5126 Marston Lane<br>West Palm Beach, FL 33411</p>
    <ul class="contact-list">
      <li><svg viewBox="0 0 10 10"><path d="M2 0.5 L3.8 2.6 L2.9 3.8 Q4 6 6.2 7.1 L7.4 6.2 L9.5 8 L8.3 9.5 Q1 8 0.5 1.7 Z"/></svg>844-GR-WHEEL</li>
      <li><svg viewBox="0 0 10 10"><rect x="0.5" y="3" width="9" height="6" rx="1"/><rect x="2.5" y="0.5" width="5" height="3"/></svg>561-278-9053</li>
      <li><svg viewBox="0 0 10 10"><path d="M2.5 0 H7.5 A1 1 0 0 1 8.5 1 V9 A1 1 0 0 1 7.5 10 H2.5 A1 1 0 0 1 1.5 9 V1 A1 1 0 0 1 2.5 0 Z M3 1.5 V8 H7 V1.5 Z"/></svg>123-456-7890</li>
      <li><svg viewBox="0 0 10 10"><path d="M0 2 H10 V8.5 H0 Z" /><path d="M0 2 L5 5.6 L10 2" stroke="#f3f3f3" stroke-width="0.9" fill="none"/></svg>info@graniterim-example.com</li>
      <li><svg viewBox="0 0 10 10"><circle cx="5" cy="5" r="4.8"/><path d="M1 4 H9 M1 6.5 H9 M5 0.3 Q2.3 5 5 9.7 M5 0.3 Q7.7 5 5 9.7" stroke="#f3f3f3" stroke-width="0.7" fill="none"/></svg>www.graniterimsupply-example.com</li>
    </ul>
  </section>

  <section class="card card-back" aria-label="Card back">
    <div class="watermark" aria-hidden="true">GRANITE<br>RIM</div>
    <div class="back-block specializing">
      <h3 class="back-heading">SPECIALIZING IN NEW AND<br>USED TIRES &amp; WHEELS FOR:</h3>
      <ul class="back-list">
        <li>Loaders</li>
        <li>Skid Steers</li>
        <li>TelehandlersBoom Lifts</li>
        <li>Forklifs and more</li>
      </ul>
    </div>
    <div class="back-block specialty">
      <h3 class="back-heading lg">SPECIALTY SERVICES</h3>
      <ul class="back-list">
        <li>Foam Filling Tires</li>
        <li>Largest Tire Press in SE</li>
        <li>ONSITE Forklift Tire Press</li>
        <li>Boom Truck Services</li>
        <li>Rubber Tracks</li>
      </ul>
    </div>
    <div class="back-block downtime">
      <h3 class="back-heading lg">ELIMINATING DOWNTIME</h3>
      <p>Wheel Exchange Program for New<br>&amp; Used Foam<br>Filled and Solid Rubber Tires</p>
    </div>
  </section>
</body>
</html>
```